Very new and innovative Web design for Property managers of Vacation rentals

We are looking for a new website design for travel agencies and property managers specialised on vacation rentals business, holiday villas and apartments.

The end users of this website are travellers who are looking for a vacation home for their next holiday: this is the reason why the website must be easy to use, attractive, professional, possibly elegant and focused on get new reservations.

This is a draft of our current website: https://intro3.kelumsito.com/
Please consider that we would like to have proposals with a totally different and innovative layout, surprise us!

These are the pages of the website:
• Homepage: feel free to redesign all the homepage as you wish, surprise us with something very new! Please consider that Property manager/Travel agencies usually want to have the opportunity to put in evidence groups of houses with specific characteristics (eg. villas with private swimming pool, apartment in big/small towns, villas with air co, etc…), destinations and tourist areas, and sometimes experiences or activities (please consider that the website layout must be suitable even if some of the previous sections are not used).
• Search page: we’d like to organise the results of the search page in three different ways:
o Grid
o Map
o List
• Property page: to illustrate the characteristics, descriptions, images, …. of the property. It is very important to put in evidence images of the property and to maintain the booking form (and the other call to action bottom – eg. whatsapp) always visible
• Custom pages: static pages composed usually by text, images and call to actions
• Contact us (general form)
• Info request (specific of a property form)
• Booking process
• Blog, organised in four pages:
o Home Page – introduction to the blog
o List of articles
o Single article
o Site Map (presentation of categories and sub-categories)

If possible, we’d prefer to receive the material in Adobe XD or similar so that we can obtain the three versions:
- smartphone
- tablet
- desktop

The website will be then developed in Bootstrap: as a result we’ll need the icons in SVG format (or the library used)

In attachment you can find the map of the website pages

```html
<!DOCTYPE html>
<html lang="en">
<head>
<meta charset="utf-8">
<title>Staylane – Blog Details</title>
<link href="https://fonts.googleapis.com/css2?family=Playfair+Display:wght@400;700&family=Montserrat:wght@400;500;600&display=swap" rel="stylesheet">
<style>
:root{
  --stage:#5d7a70;
  --green:#14b07f;
  --ink:#222;
  --muted:#8a8f94;
  --line:#e3e5e8;
  --footer:#1c1c1c;
  --footer-text:#b9bcbf;
  --panel:#e9edf5;
  --white:#fff;
}
*{box-sizing:border-box;margin:0;padding:0}
html,body{width:881px;height:1200px;overflow:hidden}
body{background:var(--stage);font-family:"Montserrat",sans-serif;color:var(--ink);position:relative}
.serif{font-family:"Playfair Display",serif}
a{color:inherit;text-decoration:none}

/* ---------- Desktop page ---------- */
.desktop{position:absolute;left:34px;top:150px;width:500px;background:var(--white);box-shadow:0 6px 24px rgba(0,0,0,.2)}
.d-header{height:40px;position:relative;border-bottom:1px solid var(--line)}
.logo{display:flex;align-items:center;gap:5px;font-weight:500;color:var(--green)}
.logo-dot{width:12px;height:12px;border-radius:50%;background:var(--green)}
.d-header .logo{position:absolute;left:46px;top:12px;font-size:12px}
.d-utility{position:absolute;right:0;top:0;height:16px;width:150px;background:var(--green);clip-path:polygon(10% 0,100% 0,100% 100%,0 100%);display:flex;justify-content:flex-end;align-items:center;gap:10px;padding-right:22px;font-size:4.5px;font-weight:600;color:var(--white);letter-spacing:.2px}
.d-nav{position:absolute;right:46px;top:26px;display:flex;gap:22px;font-size:5px;color:#444}
.d-hero{height:118px;background:linear-gradient(100deg,#5b6356 0%,#414a52 45%,#33414d 100%);display:flex;align-items:center;justify-content:center}
.d-hero h1{color:var(--white);font-size:18px;font-weight:700;letter-spacing:.3px}
.crumb{font-size:4.5px;color:var(--muted);padding:14px 46px 0}
.crumb b{color:var(--ink);font-weight:500}
.d-main{display:flex;justify-content:space-between;padding:20px 46px 26px}
.d-article{width:268px}
.photo{background:linear-gradient(120deg,#7a2a2a 0%,#c59a64 40%,#e7d7b8 65%,#9fc4c5 100%);border-radius:2px}
.d-article .photo{width:232px;height:162px}
.meta{font-size:4.5px;margin-top:9px;color:#333}
.meta span{margin:0 5px}
.d-article h2{font-size:11px;font-weight:400;line-height:1.25;margin-top:12px;width:210px}
.body-text{font-size:4.6px;line-height:1.75;color:#777;margin-top:9px}
.share{display:flex;gap:4px;margin-top:14px}
.share i{width:11px;height:11px;border:1px solid var(--line);display:block}
.section-title{font-size:8px;font-weight:400;letter-spacing:.3px}
.d-article .section-title{margin-top:46px}
.d-form{margin-top:12px;width:203px}
.row{display:flex;gap:4px;margin-bottom:6px}
.field{flex:1;height:16px;border:1px solid var(--line);font-size:3.8px;color:var(--muted);padding:5px 3px}
.check{font-size:3.8px;color:var(--muted);margin:4px 0 10px;display:flex;gap:3px;align-items:center}
.check i{width:5px;height:5px;border:1px solid var(--line);display:block}
.area{height:50px}
.btn{display:inline-block;background:var(--green);color:var(--white);font-weight:600}
.d-form .btn{font-size:4.5px;padding:6px 8px;margin-top:6px}
.d-side{width:100px}
.box{border:1px solid var(--line);padding:9px 7px;margin-bottom:14px}
.cats li{list-style:none;display:flex;justify-content:space-between;font-size:4.5px;color:#444;margin-top:8.2px}
.search{margin-top:9px;height:14px;border:1px solid #bbb;border-radius:3px;font-size:3.8px;color:var(--muted);padding:4px 5px;display:flex;justify-content:space-between;align-items:center}
.tags{display:flex;flex-wrap:wrap;gap:2px;margin-top:9px}
.tags span{border:1px solid var(--line);font-size:3.4px;color:#777;padding:3px 4px}
.d-footer{background:var(--footer);color:var(--footer-text);height:136px;position:relative;font-size:4.5px}
.d-footer .logo{position:absolute;left:46px;top:52px;font-size:9px}
.d-cols{position:absolute;left:138px;top:22px;display:flex;gap:36px}
.d-cols h4{font-family:"Playfair Display",serif;font-weight:400;font-size:6px;color:var(--white);margin-bottom:7px}
.d-cols p{margin-bottom:5px;line-height:1.3}
.copy{position:absolute;left:0;right:0;bottom:18px;text-align:center;font-size:3.6px}
.copy b,.m-copy b{color:var(--white);font-weight:500}
.social{display:flex;align-items:center;gap:4px}
.social i{width:8px;height:8px;border-radius:50%;background:var(--white);display:block}

/* ---------- Mobile page ---------- */
.mobile{position:absolute;left:606px;top:24px;width:238px;background:var(--white);box-shadow:0 6px 24px rgba(0,0,0,.2)}
.m-logo{height:32px;display:flex;justify-content:center;align-items:center}
.m-logo .logo{font-size:10px}
.m-bar{height:18px;background:var(--green);display:flex;justify-content:space-between;align-items:center;padding:0 9px;color:var(--white);font-size:5px;font-weight:600}
.burger{width:10px;height:7px;border-top:1.2px solid var(--white);border-bottom:1.2px solid var(--white);position:relative}
.burger::after{content:"";position:absolute;left:0;right:0;top:2px;border-top:1.2px solid var(--white)}
.m-hero{height:40px;background:linear-gradient(100deg,#5b6356,#3b4650 60%,#33414d);display:flex;align-items:center;justify-content:center}
.m-hero h1{color:var(--white);font-size:6.5px;font-weight:700}
.m-crumb{text-align:center;font-size:5.5px;color:var(--muted);padding:6px 0}
.m-crumb b{color:var(--ink);font-weight:500}
.mobile .photo{height:128px;border-radius:0}
.m-pad{padding:0 5px}
.mobile .meta{font-size:4.6px;margin-top:7px}
.mobile h2{font-size:8.5px;font-weight:400;line-height:1.25;margin-top:8px}
.mobile .body-text{font-size:4.3px;line-height:1.6;margin-top:5px}
.mobile .section-title{font-size:7px;margin-top:10px}
.m-form{margin-top:6px}
.m-form .field{height:17px;margin-bottom:4px;font-size:4.3px;padding:6px 5px}
.m-form .check{font-size:3.8px;margin:2px 0 6px}
.m-form .area{height:52px}
.m-form .btn{font-size:4.2px;padding:6px 6px;margin-top:4px}
.accordion{margin-top:14px;padding-bottom:10px}
.accordion div{background:var(--panel);height:17px;margin-bottom:5px;display:flex;justify-content:space-between;align-items:center;padding:0 7px;font-family:"Playfair Display",serif;font-size:6.5px}
.m-footer{background:var(--footer);color:var(--footer-text);padding:12px 5px 10px;font-size:5.2px}
.m-footer h4{font-family:"Playfair Display",serif;font-weight:400;font-size:7.5px;color:var(--white);margin:0 0 7px}
.m-footer p{margin-bottom:5.5px;line-height:1.3}
.m-footer .group{margin-bottom:10px}
.pin{display:flex;gap:4px}
.pin svg{flex:none;margin-top:1px}
.m-social p{display:flex;align-items:center;gap:5px}
.m-social i{width:10px;height:10px;border-radius:50%;background:var(--white);display:block}
.m-brand{display:flex;flex-direction:column;align-items:center;margin-top:14px}
.m-brand .logo{font-size:8px}
.m-copy{font-size:3.8px;margin-top:4px}
</style>
</head>
<body>

<!-- Desktop version -->
<section class="desktop" aria-label="Blog details page, desktop">
  <header class="d-header">
    <div class="logo"><span class="logo-dot"></span>Staylane</div>
    <div class="d-utility"><span>LOGIN</span><span>WHISHLIST</span><span>EN ˅</span></div>
    <nav class="d-nav"><a>HOME</a><a>SEARCH</a><a>PROPERTY</a><a>CUSTOM</a><a>CONTACT US</a></nav>
  </header>
  <div class="d-hero" role="img" aria-label="Seaside castle on a cliff with a boat at sea"><h1 class="serif">BLOG DETAILS</h1></div>
  <p class="crumb">Home / Blog / <b>Blog Details</b></p>
  <div class="d-main">
    <article class="d-article">
      <div class="photo" role="img" aria-label="Guest checking in at a hotel reception desk"></div>
      <p class="meta">Mara Ellis<span>|</span>December 4, 2020<span>|</span>0 Comments</p>
      <h2 class="serif">One who avoids a pain that produces no resultant pleasure</h2>
      <p class="body-text">Sed ut perspiciatis unde omnis iste natus error sit voluptatem accusantium doloremque laudantium, totam rem aperiam, eaque ipsa quae ab illo inventore veritatis et quasi architecto beatae vitae dicta sunt explicabo. Nemo enim ipsam voluptatem quia voluptas sit aspernatur aut odit aut fugit, sed quia consequuntur magni dolores eos qui ratione voluptatem sequi nesciunt. Neque porro quisquam est, qui dolorem ipsum quia dolor sit amet, consectetur, adipisci velit, sed quia non numquam eius modi tempora incidunt ut labore et dolore magnam aliquam quaerat voluptatem.</p>
      <div class="share"><i></i><i></i><i></i><i></i><i></i><i></i></div>
      <h3 class="section-title serif">LEAVE COMMENT</h3>
      <form class="d-form">
        <div class="row"><div class="field">Your Name:</div><div class="field">Email:</div></div>
        <p class="check"><i></i>Save my name, email, and website in this browser for the next time I comment.</p>
        <div class="row"><div class="field">Phone:</div><div class="field">Website:</div></div>
        <div class="field area">Comments:</div>
        <span class="btn">Post Comments</span>
      </form>
    </article>
    <aside class="d-side">
      <div class="box">
        <h3 class="section-title serif">CATEGORIES</h3>
        <ul class="cats">
          <li>Consectetur Adipiscing<span>+</span></li><li>Eget Tempor<span>+</span></li><li>Lobortis Dictum<span>+</span></li><li>Tempus Fermentum<span>+</span></li><li>Quisque<span>+</span></li>
          <li>Consectetur Adipiscing<span>+</span></li><li>Eget Tempor<span>+</span></li><li>Lobortis Dictum<span>+</span></li><li>Tempus Fermentum<span>+</span></li><li>Quisque<span>+</span></li>
        </ul>
      </div>
      <div class="box">
        <h3 class="section-title serif">SEARCH</h3>
        <div class="search">Search here
          <svg width="5" height="5" viewBox="0 0 10 10"><circle cx="4" cy="4" r="3" fill="none" stroke="#333" stroke-width="1.4"/><line x1="6.3" y1="6.3" x2="9.3" y2="9.3" stroke="#333" stroke-width="1.4"/></svg>
        </div>
      </div>
      <div class="box">
        <h3 class="section-title serif">POPULAR TAGS</h3>
        <div class="tags"><span>AGENCY</span><span>BUSINESS</span><span>CLEAN</span><span>CREATIVE</span><span>DESIGN</span><span>MODERN</span><span>POPULAR</span></div>
      </div>
    </aside>
  </div>
  <footer class="d-footer">
    <div class="logo"><span class="logo-dot"></span>Staylane</div>
    <div class="d-cols">
      <div><h4>Quick Links</h4><p>Home</p><p>Search</p><p>Property</p><p>Custom</p><p>Contact Us</p></div>
      <div><h4>Company</h4><p>Privacy Policies</p><p>Reservation Policies</p><p>Cookie Policy</p></div>
      <div><h4>Contact Us</h4><p>Via delle Rose 42 50100<br>Borgo Alto, Toscana (Italy)</p><p>+39 055 0199 482</p><p>hello@staylane.example</p></div>
      <div><h4>Follow Us</h4><p class="social"><i></i>Friendbook</p><p class="social"><i></i>Chirper</p><p class="social"><i></i>Snapgram</p></div>
    </div>
    <p class="copy">Copyright © 2021 <b>Staylane</b>. All rights reserved.</p>
  </footer>
</section>

<!-- Mobile version -->
<section class="mobile" aria-label="Blog details page, mobile">
  <div class="m-logo"><div class="logo"><span class="logo-dot"></span>Staylane</div></div>
  <div class="m-bar"><span class="burger"></span><span>♡ &nbsp;EN ˅</span></div>
  <div class="m-hero" role="img" aria-label="Seaside castle on a cliff"><h1 class="serif">BLOG DETAILS</h1></div>
  <p class="m-crumb">Home / Blog / <b>Blog Details</b></p>
  <div class="photo" role="img" aria-label="Guest checking in at a hotel reception desk"></div>
  <div class="m-pad">
    <p class="meta">Mara Ellis <span>|</span> December 4, 2020 <span>|</span> 0 Comments</p>
    <h2 class="serif">One who avoids a pain that produces no resultant pleasure</h2>
    <p class="body-text">Sed ut perspiciatis unde omnis iste natus error sit voluptatem qui ratione voluptatem sequi nesciunt. Neque porro quisquam est, qui dolorem ipsum quia dolor sit amet, consectetur, adipisci velit, sed quia non numquam eius modi tempora incidunt ut labore et dolore magnam aliquam quaerat voluptatem.</p>
    <h3 class="section-title serif">LEAVE COMMENT</h3>
    <form class="m-form">
      <div class="field">Your Name:</div><div class="field">Email:</div><div class="field">Phone:</div><div class="field">Website:</div>
      <p class="check"><i></i>Save my name, email, and website in this browser for the next time I comment.</p>
      <div class="field area">Comments:</div>
      <span class="btn">Post Comments</span>
    </form>
    <div class="accordion"><div>CATEGORIES<span>›</span></div><div>SEARCH<span>›</span></div><div>POPULAR TAGS<span>›</span></div></div>
  </div>
  <footer class="m-footer">
    <div class="group"><h4>Quick Links</h4><p>Home</p><p>Search</p><p>Property</p><p>Custom</p><p>Contact Us</p></div>
    <div class="group"><h4>Company</h4><p>Privacy Policies</p><p>Reservation Policies</p><p>Cookie Policy</p></div>
    <div class="group"><h4>Contact Us</h4>
      <p class="pin"><svg width="5" height="6" viewBox="0 0 10 12"><path d="M5 0a4 4 0 0 1 4 4c0 3-4 8-4 8S1 7 1 4a4 4 0 0 1 4-4z" fill="#fff"/></svg>Via delle Rose 42 50100<br>Borgo Alto, Toscana (Italy)</p>
      <p class="pin"><svg width="5" height="6" viewBox="0 0 10 10"><path d="M2 0l2 2-1 2c1 1 2 2 3 3l2-1 2 2-2 2C4 10 0 6 0 2z" fill="#fff"/></svg>+39 055 0199 482</p>
      <p class="pin"><svg width="6" height="5" viewBox="0 0 12 9"><rect width="12" height="9" fill="#fff"/><path d="M0 0l6 5 6-5" fill="none" stroke="#1c1c1c"/></svg>hello@staylane.example</p>
    </div>
    <div class="group m-social"><h4>Follow Us</h4><p><i></i>Friendbook</p><p><i></i>Chirper</p><p><i></i>Snapgram</p></div>
    <div class="m-brand"><div class="logo"><span class="logo-dot"></span>Staylane</div><p class="m-copy">Copyright © 2021 <b>Staylane</b>. All rights reserved.</p></div>
  </footer>
</section>

</body>
</html>
```